Coastline Premier Retreats Business Card Design

Design a business card for Coastline Premier Retreats. Look at the website for colors and reference. Card should have logo, name, title, office number, mobile number, email, URL and a tagline like, "Luxury Hotel & Resort Email Marketing" (This might change).

https://www.coastlinepremierretreats.example

The rest I will leave up to your imagination.

Contact Information for Business Card

Logo, name, title, office number, mobile number, email, URL and a tagline like, "Luxury Hotel & Resort Email Marketing" (This might change).

```html
<!DOCTYPE html>
<html lang="en">
<head>
<meta charset="utf-8">
<title>Coastline Premier Retreats – Business Card</title>
<link rel="stylesheet" href="https://fonts.googleapis.com/css2?family=Arimo:wght@400;700&family=Montserrat:wght@400&display=swap">
<style>
  :root {
    --page-bg: #121212;
    --card-bg: #1c1c1c;
    --accent: #e8731a;
    --text-light: #f2f2f2;
    --logo-grey: #5e5e5e;
  }
  * { margin: 0; padding: 0; box-sizing: border-box; }
  html, body {
    width: 1200px;
    height: 1059px;
    overflow: hidden;
    background: var(--page-bg);
    font-family: "Arimo", Arial, sans-serif;
  }
  .canvas { position: relative; width: 1200px; height: 1059px; }

  .card {
    position: absolute;
    background: var(--card-bg);
  }
  .card--front { left: 257px; top: 89px; width: 687px; height: 390px; }
  .card--back  { left: 253px; top: 546px; width: 694px; height: 394px; }

  .frame {
    position: absolute;
    left: 22px; top: 22px;
    width: 642px; height: 336px;
    border: 2px solid var(--accent);
  }
  .tagline {
    position: absolute;
    left: 177px; top: 346px;
    width: 333px;
    background: var(--card-bg);
    color: var(--accent);
    font-size: 17px;
    line-height: 22px;
    text-align: center;
    white-space: nowrap;
  }

  .identity {
    position: absolute;
    right: 372px; top: 143px;
    text-align: right;
    color: var(--text-light);
    white-space: nowrap;
  }
  .identity__name {
    color: var(--accent);
    font-weight: 700;
    font-size: 29px;
    line-height: 34px;
    letter-spacing: 0.5px;
  }
  .identity__title {
    font-family: "Montserrat", Arial, sans-serif;
    font-size: 16px;
    line-height: 20px;
    margin-bottom: 6px;
  }
  .identity__address { font-size: 16px; line-height: 21px; }

  .divider {
    position: absolute;
    left: 340px; top: 149px;
    width: 1.5px; height: 91px;
    background: var(--accent);
  }

  .contacts {
    position: absolute;
    left: 368px; top: 144px;
    list-style: none;
    color: var(--text-light);
    font-size: 14.5px;
    line-height: 26.3px;
    white-space: nowrap;
  }
  .contacts li { display: flex; align-items: center; }
  .contacts svg { width: 12px; height: 12px; margin-right: 7px; fill: var(--accent); flex: none; }

  .brand-mark {
    position: absolute;
    left: 0; right: 0; top: 180px;
    text-align: center;
    color: var(--logo-grey);
    font-weight: 700;
    font-size: 30px;
    letter-spacing: 1px;
    white-space: nowrap;
  }
</style>
</head>
<body>
<main class="canvas">

  <section class="card card--front" aria-label="Business card front">
    <div class="frame"></div>
    <p class="tagline">Luxury Hotel &amp; Resort Email Marketing</p>

    <div class="identity">
      <h1 class="identity__name">MARCUS HALE</h1>
      <p class="identity__title">CEO/Founder</p>
      <p class="identity__address">Po Box, 48 B Harbor Rd<br>Seaview Bay, CA 90000</p>
    </div>

    <div class="divider"></div>

    <ul class="contacts">
      <li>
        <svg viewBox="0 0 12 12" aria-hidden="true"><path d="M3.5 0h5a1 1 0 0 1 1 1v10a1 1 0 0 1-1 1h-5a1 1 0 0 1-1-1V1a1 1 0 0 1 1-1zm.3 1.4v7.8h4.4V1.4zM6 9.8a.7.7 0 1 0 0 1.4.7.7 0 0 0 0-1.4z"/></svg>
        555.014.2290
      </li>
      <li>
        <svg viewBox="0 0 12 12" aria-hidden="true"><path d="M0 4.5C1.5 2.5 10.5 2.5 12 4.5v1.5H9V4.8C7.5 4.3 4.5 4.3 3 4.8V6H0zM2.5 7.5 4 5.5h4l1.5 2V11h-7z"/></svg>
        +34 600 000 417
      </li>
      <li>
        <svg viewBox="0 0 12 12" aria-hidden="true"><path d="M0 4 6 0l6 4v8H0zm1.2 1v5.8h9.6V5L6 8z"/></svg>
        info@coastlinepremierretreats.example
      </li>
      <li>
        <svg viewBox="0 0 12 12" aria-hidden="true"><path d="M6 0a6 6 0 1 0 0 12A6 6 0 0 0 6 0zM2.5 3.5 5 2.5l1 1.5-1.5 2L5 8 3.5 9.5 2 6zm5 .5 2-1 1 3-1.5 3-1.5-1.5.5-2z"/></svg>
        www.coastlinepremierretreats.example
      </li>
    </ul>
  </section>

  <section class="card card--back" aria-label="Business card back">
    <p class="brand-mark">Coastline Premier Retreats</p>
  </section>

</main>
</body>
</html>
```